Academic and Business book cover

I need a book cover for my academic and business book.
The focus is in international / global negotiation and influence (how to negotiate across cultures).
The book will be published on Zelvorn, both in Vaspet and printed edition. therefore I need something that works under Zelvorn guidelines.The final design should be elegant and still be able to stand out against the competition.
I would like to have orange+grey for the text colors on the cover, even if different options are welcome.
Title and my name are in the attached word doc.

Target Market(s)

graduates, Phds, from international business schools. Managers

Industry/Entity Type

Business

Font styles to use
Serif
Sans Serif

Colors

Designer to choose colors to be used in the design.

Requirements
Must have
• The title and my name should have elegant fonts.
Nice to have
• pictures of the world that don't have the "usual" Europe in the centre.

```html
<!DOCTYPE html>
<html lang="en">
<head>
<meta charset="utf-8">
<title>The 5Cs Compass – Cover Options</title>
<link rel="stylesheet" href="https://fonts.googleapis.com/css2?family=Arimo:wght@400;700&display=swap">
<style>
  :root {
    --page: #ffffff;
    --cover: #18181d;
    --orange: #f4a63a;
    --text-light: #e9e9ec;
    --tab-grey: #48474c;
    --band-blue: #2f5883;
    --label-grey: #a9a9ab;
    --art-warm: #d39a55;
    --art-green: #5f9f78;
    --art-blue: #35608a;
  }
  * { box-sizing: border-box; margin: 0; padding: 0; }
  html, body { width: 1200px; height: 1000px; overflow: hidden; background: var(--page); }
  body { position: relative; font-family: "Arimo", Arial, sans-serif; }

  .option-label {
    position: absolute;
    font-size: 34px;
    font-weight: 700;
    color: var(--label-grey);
    line-height: 1;
  }

  .cover {
    position: absolute;
    width: 286px;
    height: 457px;
    background: var(--cover);
    overflow: hidden;
  }
  .cover svg { display: block; }

  .back-copy {
    position: absolute;
    left: 23px;
    width: 240px;
    font-size: 6.3px;
    line-height: 10.6px;
    color: var(--text-light);
  }
  .back-copy em { font-style: italic; }
  .back-copy .author-name { color: var(--orange); font-weight: 700; }
  .rule {
    position: absolute;
    left: 23px;
    width: 236px;
    height: 2px;
    background: var(--orange);
  }
  .back-band {
    position: absolute;
    left: 0;
    width: 100%;
    background: var(--band-blue);
  }

  .title { font-family: "Arimo", Arial, sans-serif; font-weight: 700; fill: var(--orange); }
  .subtitle { font-family: "Arimo", Arial, sans-serif; fill: var(--text-light); }
  .author { font-family: "Arimo", Arial, sans-serif; fill: var(--orange); }
</style>
</head>
<body>

<svg width="0" height="0" style="position:absolute">
  <defs>
    <radialGradient id="art-tones" cx="50%" cy="50%" r="60%">
      <stop offset="0%" stop-color="var(--art-warm)"/>
      <stop offset="60%" stop-color="var(--art-green)"/>
      <stop offset="100%" stop-color="var(--art-blue)"/>
    </radialGradient>
  </defs>
</svg>

<!-- Back cover A -->
<div class="cover back back-a" style="left:242px; top:20px;">
  <div class="rule" style="top:52px;"></div>
  <p class="back-copy" style="top:57px;">
    Western notions of negotiation and influence are coming under question: old familiar concepts, such as <em>power</em>, <em>interests</em>, and above all, <em>BATNA</em>, take on different meanings in an international context.<br>
    Adopting an interdisciplinary approach and staying away from academic jargon, and conventional generalizations, the book is meant to provide graduates and managers with a framework for negotiating and influencing across cultures.<br>
    The goal is to overcome Western (particularly US) ethnocentrism, moving out of laboratory simulations and providing a model based on real life exposure to international negotiations and managerial challenges.
  </p>
  <div class="rule" style="top:183px;"></div>
  <p class="back-copy" style="top:189px;">
    <span class="author-name">Arvind K. Malhar</span> is Professor of Cultural Management at the Lombard Institute in Milan, Italy, and founder of Tratavia, a management consultancy firm that assists companies in international negotiations and global teams performance improvement. He has previously lived and worked in eight countries and four different continents, leading cross functional teams implementing post M&amp;A integration strategies and managing commercial and marketing organizations in Europe, North &amp; South America, Middle East and South &amp; East Asia.
  </p>
</div>
<span class="option-label" style="left:194px; top:452px;">1</span>

<!-- Front cover A -->
<div class="cover front front-a" style="left:669px; top:20px;">
  <svg width="286" height="457" viewBox="0 0 286 457">
    <rect class="tab" x="0" y="46" width="26" height="27" fill="var(--tab-grey)"/>
    <rect class="tab" x="259" y="46" width="27" height="27" fill="var(--tab-grey)"/>
    <text class="title" x="143" y="67" font-size="20" text-anchor="middle">The 5Cs Compass</text>
    <text class="subtitle" x="141" y="98" font-size="14.5" text-anchor="middle">Practical Persuasion and Dealmaking</text>
    <text class="subtitle" x="146" y="121" font-size="14.5" text-anchor="middle">Methods for Cross-Border Success</text>

    <rect class="cover-art" x="49" y="143" width="188" height="260" fill="url(#art-tones)" role="img" aria-label="Illustration of a world globe centred on the Americas within overlapping coloured bands"/>

    <text class="author" x="143" y="434" font-size="15" text-anchor="middle">Arvind K. Malhar</text>
  </svg>
</div>
<span class="option-label" style="left:630px; top:452px;">2</span>

<!-- Back cover B -->
<div class="cover back back-b" style="left:242px; top:515px;">
  <p class="back-copy" style="top:53px;">
    Western notions of negotiation and influence are coming under question: old familiar concepts, such as <em>power</em>, <em>interests</em>, and above all, <em>BATNA</em>, take on different meanings in an international context.<br>
    Adopting an interdisciplinary approach and staying away from academic jargon, and conventional generalizations, the book is meant to provide graduates and managers with a framework for negotiating and influencing across cultures.<br>
    The goal is to overcome Western (particularly US) ethnocentrism, moving out of laboratory simulations and providing a model based on real life exposure to international negotiations and managerial challenges.
  </p>
  <div class="back-band" style="top:227px; height:93px;"></div>
  <p class="back-copy" style="top:352px;">
    <span class="author-name">Arvind K. Malhar</span> is Professor of Cultural Management at the Lombard Institute in Milan, Italy, and founder of Tratavia, a management consultancy firm that assists companies in international negotiations and global teams performance improvement. He has previously lived and worked in eight countries and four different continents, leading cross functional teams implementing post M&amp;A integration strategies and managing commercial and marketing organizations in Europe, North &amp; South America, Middle East and South &amp; East Asia.
  </p>
</div>
<span class="option-label" style="left:199px; top:942px;">3</span>

<!-- Front cover B -->
<div class="cover front front-b" style="left:669px; top:515px;">
  <svg width="286" height="457" viewBox="0 0 286 457">
    <rect class="tab" x="0" y="46" width="26" height="27" fill="var(--tab-grey)"/>
    <rect class="tab" x="259" y="46" width="27" height="27" fill="var(--tab-grey)"/>
    <text class="title" x="143" y="67" font-size="20" text-anchor="middle">The 5Cs Compass</text>
    <text class="subtitle" x="141" y="98" font-size="14.5" font-weight="700" text-anchor="middle">Practical Persuasion and Dealmaking</text>
    <text class="subtitle" x="146" y="121" font-size="14.5" font-weight="700" text-anchor="middle">Methods for Cross-Border Success</text>

    <rect class="cover-art" x="49" y="143" width="188" height="262" fill="url(#art-tones)" role="img" aria-label="Illustration of a world globe centred on the Americas within overlapping coloured bands"/>

    <text class="author" x="143" y="436" font-size="15" font-weight="700" text-anchor="middle">Arvind K. Malhar</text>
  </svg>
</div>
<span class="option-label" style="left:623px; top:946px;">4</span>

</body>
</html>
```